hello! I need a very simple modern business card for a new venture called The Quiet Harbour Retreats. It's the very first Tech-Free retreat in Asia!

The concept is very unique. Basically a group of 12-15 people would go on a 3 to 4 days retreat where no phone or internet is allowed. The first retreat will take place in a beautiful villa in Bali by the sea. It will include yoga, meditation, art & writing workshops, swimming, hiking, cooking, healthy vegetarian meals, etc.

Reason: Thanks for your submissions. I still haven't found exactly what I'm after but the designs that haven't be eliminated are getting close.. Please keep in mind that it should be a simple, modern and upmarket business card. Thanks

Target Market(s)

Both men and women who would like to disconnect from life, computer and phone for 3/4 days. They can be either local or expats but based in Asia (Singapore, Hong Kong).
Client will have to pay for their own flight and then the price is around US$600 for a 3-day retreat including everything (accommodation, food, activities). It means clients already have a good income. They are usually working in marketing, advertising, digital media, public relations.

Industry/Entity Type

Internet

Font styles to use
Other font styles liked:
• anything modern you like

Colors
acd036
9bcb3c
f37022
f68d4d
1b1b1b
333333
acd037

Requirements
Must have
• Name: Rell Vonta
Position: #screenwanderer
Company: The Quiet Harbour Retreats (asia should be smaller than the rest)
- Email button - quietharbourretreats@mailora.com
- Pagenook button - www.pagenook.com/quietharbourretreats
- Ticketvale button - www.quietharbourretreats.ticketvale.com
Nice to have
• You can use my logo attached but it's something I designed quickly on Power Point so it would be nice to include your own version.
Should not have
• anything tacky or girly or childish. thanks

```html
<!DOCTYPE html>
<html lang="en">
<head>
<meta charset="utf-8">
<title>The Quiet Harbour Retreats — Business Card</title>
<link href="https://fonts.googleapis.com/css2?family=Questrial&display=swap" rel="stylesheet">
<style>
  :root {
    --page-bg: #f4f4f4;
    --page-glow: #ffffff;
    --card-orange: #f68d4d;
    --card-slate: #4e4d4e;
    --slate-deep: #3a393a;
    --leaf: #acd036;
    --leaf-dark: #7e9e22;
    --accent-orange: #f37022;
  }
  * { margin: 0; padding: 0; box-sizing: border-box; }
  html, body {
    width: 1200px;
    height: 1000px;
    overflow: hidden;
  }
  body {
    position: relative;
    background: radial-gradient(ellipse at center, var(--page-glow) 0%, var(--page-glow) 45%, var(--page-bg) 100%);
    font-family: "Questrial", "Century Gothic", sans-serif;
  }
  .card {
    position: absolute;
    left: 200px;
    width: 800px;
  }

  /* Front face */
  .card--front {
    top: 20px;
    height: 459px;
    background: var(--card-orange);
  }
  .brand {
    position: absolute;
    left: 128px;
    top: 181px;
    display: flex;
    align-items: center;
    gap: 22px;
  }
  .brand__dot {
    width: 120px;
    height: 120px;
    border-radius: 50%;
    background: var(--leaf);
    flex: none;
  }
  .brand__name {
    font-size: 32px;
    color: var(--leaf);
    white-space: nowrap;
    letter-spacing: 0.5px;
  }
  .card__footer {
    position: absolute;
    left: 0;
    bottom: 0;
    width: 100%;
    height: 38px;
    background: var(--card-slate);
    display: flex;
    align-items: center;
    justify-content: center;
  }
  .card__footer-url {
    font-size: 19px;
    color: var(--accent-orange);
    letter-spacing: 0.5px;
  }

  /* Back face */
  .card--back {
    top: 521px;
    height: 458px;
    background: var(--card-slate);
  }
  .person {
    position: absolute;
    left: 26px;
    top: 168px;
    color: var(--leaf);
  }
  .person__name {
    font-size: 62px;
    line-height: 70px;
    letter-spacing: 2px;
    white-space: nowrap;
  }
  .person__title {
    font-size: 41px;
    line-height: 46px;
    letter-spacing: 0.5px;
    white-space: nowrap;
  }
  .divider {
    position: absolute;
    left: 397px;
    top: 80px;
    width: 4px;
    height: 310px;
    background: linear-gradient(to bottom, transparent, var(--slate-deep) 20%, var(--slate-deep) 80%, transparent);
  }
  .contacts {
    position: absolute;
    left: 421px;
    top: 164px;
    list-style: none;
  }
  .contacts__item {
    display: flex;
    align-items: center;
    gap: 12px;
    height: 32px;
    margin-bottom: 15px;
  }
  .contacts__icon {
    width: 32px;
    height: 32px;
    flex: none;
  }
  .contacts__icon--square {
    width: 30px;
    height: 30px;
    border-radius: 4px;
    background: var(--leaf);
    margin-left: 1px;
  }
  .contacts__text {
    font-size: 14.5px;
    color: var(--leaf);
    letter-spacing: 0.3px;
    white-space: nowrap;
  }
</style>
</head>
<body>

  <section class="card card--front">
    <div class="brand">
      <span class="brand__dot"></span>
      <span class="brand__name">The Quiet Harbour Retreats</span>
    </div>
    <div class="card__footer">
      <span class="card__footer-url">www.quietharbourretreats.com</span>
    </div>
  </section>

  <section class="card card--back">
    <div class="person">
      <p class="person__name">Rell Vonta</p>
      <p class="person__title">#screenwanderer</p>
    </div>

    <div class="divider"></div>

    <ul class="contacts">
      <li class="contacts__item">
        <svg class="contacts__icon" viewBox="0 0 32 32" aria-hidden="true">
          <rect x="1" y="6" width="30" height="20" fill="#acd036"/>
          <path d="M2 7 L16 18 L30 7" fill="none" stroke="#4e4d4e" stroke-width="2.5"/>
          <path d="M2 25 L12 15 M30 25 L20 15" fill="none" stroke="#4e4d4e" stroke-width="2"/>
        </svg>
        <span class="contacts__text">quietharbourretreats@mailora.com</span>
      </li>
      <li class="contacts__item">
        <span class="contacts__icon contacts__icon--square"></span>
        <span class="contacts__text">www.pagenook.com/quietharbourretreats</span>
      </li>
      <li class="contacts__item">
        <span class="contacts__icon contacts__icon--square"></span>
        <span class="contacts__text">www.quietharbourretreats.ticketvale.com</span>
      </li>
    </ul>
  </section>

</body>
</html>
```